Lurvik.no is a new website about pedagogical entrepreneurship. It's main target group is teachers. The Nordic Bureau for Digital Schooling and the National Office for Learning and Classrooms are leading the project.

The web page is meant to show examples of how different methods of entrepreneurship can be used pedagogical in a learning environment. The page will also support the user with examples of different teaching programs and other examples of best practice.

Pedagogical entrepreneurship is not about business and men in suits. It's a method for learning. The focus in the design should be on school, education and new ways of learning.

The final product should be motivating and engaging, but at the same time governmental and serious. We are not looking for something "flashy" and corporate-looking, but a moderate, task-focused and clean design that state quality.

We need designs for three pages:
1 - frontpage
2 - subpage ("Metoder og undervisningsopplegg")
3 - subpage ("Små-TOPP i Vassbygd")

The interaction design for these three pages will be uploaded as an attachment.

We would like you to find inspiration in the following websites:
- www.skapekraft.no
- www.giellu.no
- www.brightfernlab.com
- www.zyx.no
(more will be added)

Please use the attached logo, and feel free to use this as an inspiration for the rest of the design.

Target Market(s)

Teachers

Industry/Entity Type

Education

Requirements
Must have
• * Header with: Logo. Main navigation. Utility navigation. Search box.
* Footer
Should not have
• Images of men in suits.
Very strong graphical elements that stands out too much (we want it clean).

```html
<!DOCTYPE html>
<html lang="en">
<head>
<meta charset="utf-8">
<title>Lurvik.no – Pedagogical entrepreneurship</title>
<link rel="stylesheet" href="https://fonts.googleapis.com/css2?family=Arimo:wght@400;700&family=PT+Sans+Narrow&display=swap">
<style>
  :root {
    --navy: #033f6b;
    --navy-deep: #02365d;
    --blue: #1580c4;
    --sky: #4fa9e2;
    --sky-light: #7cc2ee;
    --grey-band-top: #e4e4e4;
    --grey-band-mid: #f4f4f4;
    --grey-band-low: #d6d6d6;
    --ink: #111;
    --text: #444;
    --link: #145a8c;
    --rule: #c8c8c8;
    --white: #fff;
  }
  * { box-sizing: border-box; margin: 0; padding: 0; }
  html, body { width: 1200px; height: 910px; overflow: hidden; }
  body { font-family: "Arimo", Arial, sans-serif; background: var(--white); position: relative; }

  .utility-bar { position: absolute; left: 0; top: 0; width: 1200px; height: 36px; background: var(--navy); }
  .masthead {
    position: absolute; left: 0; top: 36px; width: 1200px; height: 172px;
    background:
      radial-gradient(ellipse 360px 160px at 300px 90px, rgba(120,200,245,.55), transparent 70%),
      linear-gradient(180deg, var(--sky) 0%, #2d8fd3 45%, #1676bd 100%);
    border-top: 1px solid var(--sky-light);
  }
  .search {
    position: absolute; left: 778px; top: 17px; width: 268px; height: 37px;
    background: var(--white); box-shadow: 0 2px 4px rgba(0,0,0,.35);
    display: flex; align-items: center; justify-content: space-between; padding: 0 12px 0 17px;
    font-size: 12px; color: #2a4f6d;
  }
  .brand { position: absolute; left: 155px; top: 86px; display: flex; align-items: center; gap: 26px; }
  .brand-mark { width: 58px; height: 58px; border-radius: 50%; background: var(--white); opacity: .9; }
  .brand-name { font-size: 48px; font-weight: 700; color: var(--white); letter-spacing: -1px; }

  .main-nav {
    position: absolute; left: 520px; top: 107px; width: 558px; height: 40px;
    background: linear-gradient(180deg, #0b4d7d, #063a63); border-radius: 7px;
    display: flex; align-items: center; padding-left: 30px;
  }
  .main-nav a { color: var(--white); text-decoration: none; font-size: 14px; padding: 0 14px; height: 40px; line-height: 40px; }
  .main-nav a + a { border-left: 1px solid #0f2f4b; }

  .feature-band {
    position: absolute; left: 0; top: 208px; width: 1200px; height: 245px;
    background: linear-gradient(180deg, var(--grey-band-top) 0%, var(--grey-band-mid) 45%, var(--grey-band-low) 100%);
  }
  .feature-card {
    position: absolute; top: 39px; width: 291px; height: 185px; background: linear-gradient(180deg, #fff 60%, #f1f1f1);
    border-radius: 4px; box-shadow: 1px 2px 4px rgba(0,0,0,.3); text-align: center;
  }
  .feature-card .icon { width: 70px; height: 58px; margin: 18px auto 0; border-radius: 6px; }
  .feature-card .kicker { margin-top: 11px; font-size: 15px; color: var(--link); }
  .feature-card h2 { font-weight: 400; font-size: 23px; line-height: 27px; color: var(--ink); margin-top: 4px; }
  .feature-card.learn { left: 141px; } .feature-card.learn .icon { background: linear-gradient(#3c8fe0, #1a5fb0); }
  .feature-card.plan { left: 455px; } .feature-card.plan .icon { background: linear-gradient(#8cc04a, #3d7ec8 50%, #c9572c); }
  .feature-card.inspire { left: 769px; } .feature-card.inspire .icon { background: linear-gradient(#e7a868, #3c5a86); }

  .section-title {
    position: absolute; top: 472px; height: 30px; background: var(--blue); color: var(--white);
    font-family: "PT Sans Narrow", "Arial Narrow", sans-serif; font-size: 22px; line-height: 30px; padding-left: 7px;
  }
  .get-started-title { left: 143px; width: 301px; }
  .inspiration-title { left: 480px; width: 582px; }

  .link-column { position: absolute; top: 518px; list-style: none; font-size: 14px; color: var(--text); }
  .link-column li { height: 30px; }
  .link-column li.head { font-weight: 700; color: #333; }
  .methods { left: 150px; } .plans { left: 326px; }

  .story { position: absolute; top: 519px; width: 141px; text-align: center; }
  .story .thumb { height: 100px; border: 1px solid #ddd; padding: 6px; background: var(--white); }
  .story .thumb div { height: 88px; background: linear-gradient(180deg, #b9c9d9 0%, #9a8e86 40%, #e6eaee 75%, #c9ced3 100%); }
  .story p { margin-top: 12px; font-size: 14px; line-height: 15px; color: var(--link); }

  .divider { position: absolute; left: 147px; top: 717px; width: 910px; border-top: 1px solid var(--rule); }

  .site-footer { position: absolute; left: 0; top: 730px; width: 1200px; height: 180px; background: var(--navy); color: var(--white); border-top: 2px solid var(--navy-deep); }
  .footer-col { position: absolute; list-style: none; font-size: 12px; }
  .footer-col li { height: 18px; }
  .footer-col h3 { font-weight: 400; font-size: 14px; margin-bottom: 17px; }
  .footer-col .more { font-size: 14px; margin-top: 4px; }
  .f1 { left: 151px; top: 34px; } .f1 h3 { margin-left: 1px; font-size: 14.5px; margin-bottom: 16px; }
  .f2 { left: 410px; top: 37px; } .f2 li:not(.more) { padding-left: 2px; }
  .f3 { left: 573px; top: 36px; }
  .f4 { left: 727px; top: 37px; }
</style>
</head>
<body>
  <div class="utility-bar"></div>
  <header class="masthead">
    <div class="brand">
      <span class="brand-mark"></span>
      <span class="brand-name">Lurvik</span>
    </div>
    <nav class="main-nav">
      <a href="#">BEST PRACTICE SCHOOLS</a>
      <a href="#">LURVIKOMETER</a>
      <a href="#">ABOUT LURVIK NO</a>
    </nav>
  </header>
  <form class="search" role="search">
    <span>Search</span>
    <svg width="14" height="16" viewBox="0 0 14 16"><circle cx="5" cy="5" r="3.6" fill="none" stroke="#111" stroke-width="2"/><line x1="7.5" y1="8" x2="12" y2="14" stroke="#111" stroke-width="2.6" stroke-linecap="round"/></svg>
  </form>

  <section class="feature-band">
    <a class="feature-card learn"><div class="icon" role="img" aria-label="Learn button icon"></div><p class="kicker">Learn about what, and how!</p><h2>What is pedagocical<br>entrapreneurship?</h2></a>
    <a class="feature-card plan"><div class="icon" role="img" aria-label="Stack of books icon"></div><p class="kicker">Plan Your Lessons!</p><h2>Methods and<br>teaching plans</h2></a>
    <a class="feature-card inspire"><div class="icon" role="img" aria-label="Group of people icon"></div><p class="kicker">Be inspired!</p><h2 style="font-size:20px">Good examples /<br>Best Practice</h2></a>
  </section>

  <h2 class="section-title get-started-title">Get Started!</h2>
  <ul class="link-column methods">
    <li class="head">Methods</li><li>cafe-pedagogikk</li><li>elevbedrift</li><li>Grundercamp</li><li>Story line</li><li>Real</li>
  </ul>
  <ul class="link-column plans">
    <li class="head">Teaching Plans</li><li>Teaching plan Title</li><li>Teaching plan Title</li><li>Teaching plan Title</li><li>Teaching plan Title</li><li>Teaching plan Title</li>
  </ul>

  <h2 class="section-title inspiration-title">Inspiration</h2>
  <a class="story" style="left:480px"><div class="thumb"><div role="img" aria-label="Photo of a school building in snow"></div></div><p>Små-TOPP at<br>Vassbygd School</p></a>
  <a class="story" style="left:628px"><div class="thumb"><div role="img" aria-label="Photo of a school building in snow"></div></div><p>Små-TOPP at<br>Vassbygd School</p></a>
  <a class="story" style="left:775px"><div class="thumb"><div role="img" aria-label="Photo of a school building in snow"></div></div><p>Små-TOPP at<br>Vassbygd School</p></a>
  <a class="story" style="left:922px"><div class="thumb"><div role="img" aria-label="Photo of a school building in snow"></div></div><p>Små-TOPP at<br>Vassbygd School</p></a>

  <div class="divider"></div>

  <footer class="site-footer">
    <ul class="footer-col f1"><h3>Padagogical entrepreneurship</h3><li>What is pedagogical entrepreneurship?</li><li>Science</li><li>Best Practice Schools</li><li>Lurvikometeret</li><li>About Lurvik.no</li></ul>
    <ul class="footer-col f2"><h3>Methods</h3><li>Story Line</li><li>Real</li><li>Cafe-Pedagogikk</li><li class="more">See More &gt;</li></ul>
    <ul class="footer-col f3"><h3>Teaching Plans</h3><li>Title</li><li>Title</li><li>Title</li><li class="more">See More &gt;</li></ul>
    <ul class="footer-col f4"><h3>Gode eksempler</h3><li>Små-TOPP at Vassbygd School</li><li>Små-TOPP at Vassbygd School</li><li>Små-TOPP at Vassbygd School</li><li class="more">See More &gt;</li></ul>
  </footer>
</body>
</html>
```